The Linen Loft Co

We need a business card design for our wardrobe company.
Please visit our website www.gentlelinenlofts.com to get an idea of who we are.

```html
<!DOCTYPE html>
<html lang="en">
<head>
<meta charset="utf-8">
<title>The Linen Loft Co — Business Card</title>
<link rel="stylesheet" href="https://fonts.googleapis.com/css2?family=Roboto:wght@400;500;700&display=swap">
<style>
  :root {
    --backdrop: #d9d9d9;
    --card: #ffffff;
    --ink: #111111;
    --ink-soft: #3a3a3a;
    --muted: #a6a6a6;
    --rule: #cfcfcf;
    --band: #0c0c0c;
    --band-grey: #b3b3b3;
    --on-band: #ffffff;
  }
  * { box-sizing: border-box; margin: 0; padding: 0; }
  html, body {
    width: 1200px; height: 989px; overflow: hidden;
    background: var(--backdrop);
    font-family: "Roboto", Arial, sans-serif;
  }
  .card {
    position: absolute; left: 162px; top: 228px;
    width: 884px; height: 512px;
    background: var(--card);
    overflow: hidden;
  }
  .brand {
    position: absolute; right: 54px; top: 60px;
    display: flex; align-items: center; gap: 16px;
  }
  .brand-square {
    width: 64px; height: 64px; background: var(--ink);
  }
  .brand-text { text-align: center; color: var(--ink); font-weight: 500; }
  .brand-name { font-size: 22px; letter-spacing: 0.3px; line-height: 1.2; }
  .brand-tagline { font-size: 18px; margin-top: 8px; line-height: 1.2; }

  .person { position: absolute; left: 48px; top: 298px; }
  .person-name { font-size: 34px; font-weight: 700; color: var(--ink); line-height: 1.1; }
  .person-title { font-size: 22px; color: var(--muted); line-height: 1.2; margin-top: 2px; }

  .divider {
    position: absolute; left: 50px; right: 52px; top: 372px;
    height: 2px; background: var(--rule);
  }

  .contact, .address {
    position: absolute; top: 388px;
    font-size: 22px; color: var(--ink-soft); line-height: 27px;
    font-style: normal;
  }
  .contact { left: 50px; }
  .contact-row { display: flex; align-items: center; gap: 16px; }
  .contact-row svg { width: 18px; height: 18px; fill: var(--ink); flex: none; }
  .address { right: 54px; text-align: right; }

  .footer-band { position: absolute; left: 0; bottom: 0; width: 884px; height: 40px; }
  .footer-band .grey { fill: var(--band-grey); }
  .footer-band .black { fill: var(--band); }
  .website {
    position: absolute; right: 29px; top: 478px;
    font-size: 22px; color: var(--on-band); letter-spacing: 0.2px; line-height: 27px;
  }
</style>
</head>
<body>
  <main class="card">
    <header class="brand">
      <div class="brand-square"></div>
      <div class="brand-text">
        <div class="brand-name">THE LINEN LOFT CO</div>
        <div class="brand-tagline">Folded with Quiet Care</div>
      </div>
    </header>

    <section class="person">
      <h1 class="person-name">Daniel Hart</h1>
      <p class="person-title">President</p>
    </section>

    <div class="divider"></div>

    <section class="contact">
      <div class="contact-row">
        <svg viewBox="0 0 24 24" aria-hidden="true"><path d="M6.6 10.8a15.1 15.1 0 0 0 6.6 6.6l2.2-2.2c.3-.3.7-.4 1-.2 1.1.4 2.3.6 3.6.6.6 0 1 .4 1 1V20c0 .6-.4 1-1 1C10.6 21 3 13.4 3 4c0-.6.4-1 1-1h3.5c.6 0 1 .4 1 1 0 1.3.2 2.5.6 3.6.1.3 0 .7-.2 1z"/></svg>
        <span>020 7946 0213</span>
      </div>
      <div class="contact-row">
        <svg viewBox="0 0 24 24" aria-hidden="true"><path d="M2 5h20v2l-10 7L2 7z"/><path d="M2 9l10 7 10-7v10H2z"/></svg>
        <span>info@gentlelinenlofts.com</span>
      </div>
    </section>

    <address class="address">
      Marlow House, 42 Mill Lane<br>
      London N4 3QT
    </address>

    <svg class="footer-band" viewBox="0 0 884 40" aria-hidden="true">
      <polygon class="grey" points="0,14 511,14 501,24 0,24"/>
      <polygon class="black" points="526,0 884,0 884,40 0,40 0,24 501,24"/>
    </svg>
    <div class="website">www.gentlelinenlofts.com</div>
  </main>
</body>
</html>
```